Tavel Website

Need a 4 page Drupal website - Home, About Us, Portfolio, Contact for a private equity/venture capital firm and new logo - company name is Tavel Corporation. The design should communicate - stock markets, hedge funds, deal-making, investments. The Portfolio section is to showcase the small companies we invest in. Hoping for something fresh, dynamic, even fun - no cliche financial images of New York. Not technical - but know how use Drupal content management to make text edits, blocks, articles, etc. We don't use any social media - so no chirply, Pagebook or WorkNode links. We need space for a post heron email sign-up form. Need website uploaded to my Corvane web hosting account. First time user of Sketch Plaza - have 3 other company websites that need refreshing.

```html
<!DOCTYPE html>
<html lang="en">
<head>
<meta charset="utf-8">
<title>Tavel Corporation</title>
<link href="https://fonts.googleapis.com/css2?family=Lato:ital,wght@0,400;0,700;1,400&display=swap" rel="stylesheet">
<style>
:root{
  --ink:#2e3140;
  --coral:#ec6b61;
  --coral-dark:#d9584f;
  --text:#333;
  --muted:#888;
  --band:#f4f4f4;
  --line:#e4e4e4;
  --white:#fff;
}
*{margin:0;padding:0;box-sizing:border-box}
html,body{width:682px;height:1200px;overflow:hidden;background:var(--white)}
body{position:relative;font-family:'Lato',sans-serif;color:var(--text)}
.abs{position:absolute}
.site-header{left:0;top:0;width:682px;height:50px;background:var(--ink)}
.brand{left:74px;top:15px;display:flex;align-items:center;gap:6px;color:var(--white);font-weight:700;font-size:14px}
.brand-mark{width:11px;height:11px;background:var(--coral);border-radius:2px}
.nav{top:19px;font-size:8px;color:#c9cbd3;letter-spacing:.2px}
.nav.active{color:var(--white);font-weight:700}
.signin{left:541px;top:14px;width:66px;height:21px;border-radius:11px;background:var(--coral);color:var(--white);font-size:8px;font-weight:700;display:flex;align-items:center;justify-content:center}
.hero{left:0;top:50px;width:682px;height:320px;background:linear-gradient(90deg,#6b5a50 0%,#cfcfcf 35%,#e6e6e6 60%,#bdbdbd 100%)}
.hero-shade{left:0;top:200px;width:682px;height:170px;background:linear-gradient(180deg,rgba(0,0,0,0),rgba(0,0,0,.35))}
.hero-arrow{top:188px;width:44px;height:44px;border:2px solid rgba(255,255,255,.85);border-radius:50%}
.hero-title{left:0;top:262px;width:682px;text-align:center;color:var(--white);font-size:20px;font-weight:700}
.hero-text{left:120px;top:297px;width:442px;text-align:center;color:var(--white);font-size:10.5px;line-height:15px}
.section-title{left:0;width:682px;text-align:center;font-size:14px;font-weight:700;color:var(--ink)}
.section-lead{left:130px;width:422px;text-align:center;font-size:8px;line-height:15px;color:#444}
.feature{top:458px;width:124px;text-align:center}
.feature svg{display:block;margin:0 auto}
.feature h3{font-size:11px;font-weight:400;color:var(--text);margin-top:14px}
.feature p{font-size:6.6px;line-height:11.5px;color:var(--muted);margin-top:9px}
.band{left:0;top:610px;width:682px;height:318px;background:var(--band);border-top:1px solid #eaeaea;border-bottom:1px solid #eaeaea}
.band-rule{left:200px;top:663px;width:282px;height:1px;background:var(--line)}
.video-title{left:74px;top:681px;font-size:12px}
.video-text{left:74px;top:704px;width:300px;font-size:6.6px;font-style:italic;line-height:11px;color:var(--muted)}
.video{left:74px;top:750px;width:299px;height:147px;background:linear-gradient(90deg,#eef1f5,#f6f6f6);border:1px solid #cfcfcf}
.play{left:132px;top:58px}
.signup{left:398px;top:682px;width:210px;height:214px;background:var(--coral)}
.signup h4{position:absolute;left:30px;top:14px;color:var(--white);font-size:10.5px;font-weight:700}
.signup label{position:absolute;left:12px;color:var(--white);font-size:6.6px}
.field{position:absolute;left:12px;width:186px;height:22px;background:var(--white);border-radius:2px;display:flex}
.field-icon{width:26px;border-right:1px solid #ddd;background:#f3f3f3;display:flex;align-items:center;justify-content:center}
.field span{font-size:6.6px;color:#aaa;padding-left:7px;align-self:center}
.terms{position:absolute;left:14px;top:146px;font-size:5.6px;font-style:italic;color:var(--white);display:flex;align-items:center;gap:4px}
.terms i{width:6px;height:6px;background:var(--white);display:inline-block}
.terms em{color:#ffe27a}
.signup-btn{position:absolute;left:12px;top:167px;width:186px;height:29px;background:linear-gradient(#464a5a,#2a2d3a);border-radius:2px;color:var(--white);font-size:10px;display:flex;align-items:center;justify-content:center}
.card{top:1022px;width:98px;height:76px;background:var(--white);border:1px solid #e6e6e6;display:flex;align-items:center;justify-content:center;font-weight:700;font-size:12px;color:#1f4e9c}
.card-name{top:1106px;width:98px;text-align:center;font-size:9px;color:#555}
.slide-btn{top:1048px;width:24px;height:24px;border-radius:50%;background:#c8c8c8}
.site-footer{left:0;top:1146px;width:682px;height:54px;background:var(--ink)}
.foot-nav{left:76px;top:1169px;font-size:7.5px;color:#c9cbd3;letter-spacing:.2px}
.foot-nav b{color:var(--white)}
.foot-nav span{margin:0 8px}
.copy{left:470px;top:1169px;font-size:6.6px;color:#c9cbd3}
.code{left:649px;top:1169px;font-size:6.6px;color:#c9cbd3}
</style>
</head>
<body>
<header class="abs site-header"></header>
<div class="abs brand"><span class="brand-mark"></span>TAVEL CORPORATION</div>
<div class="abs nav active" style="left:308px">HOME</div>
<div class="abs nav" style="left:353px">ABOUT US</div>
<div class="abs nav" style="left:414px">PORTFOLIO</div>
<div class="abs nav" style="left:482px">CONTACT</div>
<div class="abs signin">SIGN IN</div>

<section class="abs hero" role="img" aria-label="Photo of a smiling businesswoman holding a tablet showing financial charts"></section>
<div class="abs hero-shade"></div>
<div class="abs hero-arrow" style="left:11px"><svg width="40" height="40"><path d="M23 13l-7 7 7 7" fill="none" stroke="#fff" stroke-width="2"/></svg></div>
<div class="abs hero-arrow" style="left:625px"><svg width="40" height="40"><path d="M17 13l7 7-7 7" fill="none" stroke="#fff" stroke-width="2"/></svg></div>
<h1 class="abs hero-title">TAVEL CORPORATION</h1>
<p class="abs hero-text">Lorem Ipsum is simply dummy text of the printing and typesetting industry. Lorem Ipsum has been the industry's standard dummy text ever since the 1500.</p>

<h2 class="abs section-title" style="top:389px">ABOUT US</h2>
<p class="abs section-lead" style="top:412px">Lorem Ipsum is simply dummy text of the printing and typesetting industry. Lorem Ipsum has been the industry's standard dummy text ever since the 1500s, when an unknown.</p>

<div class="abs feature" style="left:72px">
  <svg width="60" height="56" viewBox="0 0 60 56"><rect x="2" y="2" width="56" height="40" rx="2" fill="var(--coral)"/><rect x="7" y="7" width="46" height="30" fill="#fff"/><path d="M12 30l10-10 8 6 14-12" fill="none" stroke="var(--coral)" stroke-width="2.5"/><circle cx="22" cy="20" r="2.5" fill="var(--coral)"/><circle cx="30" cy="26" r="2.5" fill="var(--coral)"/><circle cx="44" cy="14" r="2.5" fill="var(--coral)"/><path d="M24 42h12l3 8H21z" fill="var(--coral)"/><rect x="16" y="50" width="28" height="4" fill="var(--coral)"/></svg>
  <h3>Stock Markets</h3>
  <p>Augue iriure dolorum per ex, ne iisque ornatus veritus duo. Ex nobiouis integre lucilius sit, pri ea falli ludus appareat.</p>
</div>
<div class="abs feature" style="left:212px">
  <svg width="60" height="56" viewBox="0 0 60 56"><path d="M22 2h16l-4 10h-8z" fill="var(--coral)"/><path d="M24 14h12c14 8 20 20 18 30-2 8-10 10-24 10S8 52 6 44C4 34 10 22 24 14z" fill="var(--coral)"/><text x="30" y="46" text-anchor="middle" font-family="Lato,sans-serif" font-weight="700" font-size="28" fill="#fff">$</text></svg>
  <h3>Hedge Funds</h3>
  <p>Augue iriure dolorum per ex, ne iisque ornatus veritus duo. Ex nobiouis integre lucilius sit, pri ea falli ludus appareat.</p>
</div>
<div class="abs feature" style="left:348px">
  <svg width="60" height="56" viewBox="0 0 60 56"><rect x="4" y="22" width="12" height="30" fill="var(--coral)"/><path d="M18 22l12-18c4-2 7 1 6 5l-3 11h18c4 0 6 3 5 6l-5 22c-1 3-3 4-6 4H18z" fill="var(--coral)"/></svg>
  <h3>Deal-Making</h3>
  <p>Augue iriure dolorum per ex, ne iisque ornatus veritus duo. Ex nobiouis integre lucilius sit, pri ea falli ludus appareat.</p>
</div>
<div class="abs feature" style="left:486px">
  <svg width="60" height="56" viewBox="0 0 60 56"><rect x="8" y="40" width="7" height="14" fill="var(--coral)"/><rect x="18" y="34" width="7" height="20" fill="var(--coral)"/><rect x="28" y="28" width="7" height="26" fill="var(--coral)"/><rect x="38" y="20" width="7" height="34" fill="var(--coral)"/><path d="M8 36c18-4 30-12 36-24l-6-2 14-8 2 16-6-3C42 28 28 38 8 40z" fill="var(--coral)"/></svg>
  <h3>Investments</h3>
  <p>Augue iriure dolorum per ex, ne iisque ornatus veritus duo. Ex nobiouis integre lucilius sit, pri ea falli ludus appareat.</p>
</div>

<section class="abs band"></section>
<h2 class="abs section-title" style="top:633px">GET BETTER CONVERSION WITH TAVEL CORPORATION</h2>
<div class="abs band-rule"></div>
<div class="abs video-title">Watch Our Video</div>
<p class="abs video-text">Lorem ipsum dolor sit amet, consectetur adipiscing elit, sed do eiusmod tempor incididunt ut labore et dolore magna aliqua. Ut enim ad minim veniam, quis nostrud exercitation ullamco laboris nisi ut aliquip ex ea commodo consequat.</p>
<div class="abs video" role="img" aria-label="Video still of a businesswoman in front of a rising line chart">
  <svg class="abs play" width="36" height="36"><circle cx="18" cy="18" r="16" fill="rgba(255,255,255,.6)" stroke="#111" stroke-width="2"/><path d="M14 10l12 8-12 8z" fill="#111"/></svg>
</div>

<form class="abs signup">
  <svg class="abs" style="left:11px;top:11px" width="16" height="16"><rect x="1" y="3" width="12" height="12" rx="2" fill="none" stroke="#fff" stroke-width="1.5"/><path d="M6 10l8-8 1.5 1.5-8 8H6z" fill="#fff"/></svg>
  <h4>SUBSCRIBE NEWSLETTER SIGNUP</h4>
  <label style="top:48px">Your Name:</label>
  <div class="field" style="top:59px"><div class="field-icon"><svg width="8" height="8"><circle cx="4" cy="2.5" r="2" fill="#333"/><path d="M0 8c0-3 2-4 4-4s4 1 4 4z" fill="#333"/></svg></div><span>Your Name:</span></div>
  <label style="top:95px">Email Address:</label>
  <div class="field" style="top:107px"><div class="field-icon"><svg width="8" height="6"><rect width="8" height="6" fill="#333"/><path d="M0 0l4 3 4-3" fill="none" stroke="#fff" stroke-width=".8"/></svg></div><span>Email Address</span></div>
  <div class="terms"><i></i>I agree to Terms and Conditions <em>(Click open modal)</em></div>
  <div class="signup-btn">NEWSLETTER SIGNUP</div>
</form>

<h2 class="abs section-title" style="top:955px">PORTFOLIO</h2>
<p class="abs section-lead" style="top:979px">Lorem Ipsum is simply dummy text of the printing and typesetting industry. Lorem Ipsum has been the industry's standard dummy text ever since the 1500s, when an unknown.</p>
<div class="abs slide-btn" style="left:39px"><svg width="24" height="24"><path d="M14 7l-5 5 5 5" fill="none" stroke="#fff" stroke-width="2"/></svg></div>
<div class="abs slide-btn" style="left:620px"><svg width="24" height="24"><path d="M10 7l5 5-5 5" fill="none" stroke="#fff" stroke-width="2"/></svg></div>
<div class="abs card" style="left:74px">Orlena</div>
<div class="abs card" style="left:183px">Bramwell</div>
<div class="abs card" style="left:293px">Lumigrid</div>
<div class="abs card" style="left:402px">Pexaron</div>
<div class="abs card" style="left:510px">Vantrel</div>
<div class="abs card-name" style="left:74px">Orlena D/B/A</div>
<div class="abs card-name" style="left:183px">Bramwell Corp</div>
<div class="abs card-name" style="left:293px">Lumigrid Systems</div>
<div class="abs card-name" style="left:402px">Pexaron</div>
<div class="abs card-name" style="left:510px">Vantrel Inc</div>

<footer class="abs site-footer"></footer>
<nav class="abs foot-nav"><b>HOME</b><span>|</span>ABOUT US<span>|</span>PORTFOLIO<span>|</span>CONTACT</nav>
<div class="abs copy">©Tavel Corporation 2014 - All Right Reserved</div>
<div class="abs code">C4</div>
</body>
</html>
```